Dell Corvin - Acoustic Album Cover

I am a musical artist releasing my first full-length solo album. It is composed of nine original "percussive" acoustic fingerstyle songs. Some of my earlier recordings (not for this album) are available at http://www.tunelodge.net/dellcorvin for reference. I am looking for creative album art and need both a front cover and back cover/track listing for physical CD replication and online album art purposes. I am open to a more "natural" design using the pictures included in the uploaded files section or to a more artistic design that doesn't use any of the included pictures at all. The name of the album is "Driftwood", and artist is "Dell Corvin" (me). The track list is:

01) Orchard Shuffle
02) Tumbleweed
03) Glimpses of Perlow
04) Wound Up
05) Walk Along
06) The Quiet Ridge
07) Unfolding
08) Evening on Barrow Lane
09) Lucinda's Tune

Here are some album art examples from professional acoustic artists in the same style as a reference:

https://img.vidplexo.net/v/QwLmZr8NeYt/cover.jpg
http://strumvault.net/wp-content/uploads/2009/12/Low-Meadow-cover-reduced.jpg
https://plinkhouse.examplecdn.net/ImageGen.ashx?image=/media/10608/Teo-Bandry.jpg&width=500
https://files.openfolio.net/commons/1/11/Paul_Vesterby-Tidewater_album.jpg
https://direct.songrivet.net/imageserver/images/Alb.000000000/500x500.jpg
https://pics.shopvarlo.net/images/I/7Kq2mXwPzA1._SY355_.jpg
https://pics.shopvarlo.net/images/I/3Hn9bTyQcL4._SY355_.jpg

As you can see, there is a broad mix of both art-based and photograph-based album covers for artists of this style. I am open to either approach, and an example of each would be preferred if time permits.

Thank you for considering my project and for sharing your artistic talents!

-Dell

Target Market(s)

Music app listeners (Tunora, Melodex, Cadenzo) on any app which displays the album art as part of the artist information pane.

Industry/Entity Type

Music Download

Font styles to use
Serif
Sans Serif
Decorative

Colors

Designer to choose colors to be used in the design.

Requirements
Must have
• The project must have the album name and artist name on the front cover artwork, as well as the track listing on the back cover artwork.
Nice to have
• Some original, creative album artwork would be nice to have, but I would settle on well-done picture-based album designs (photos included) as well.
Should not have
• The project should not have too "stuffy" of a feel (similar to a lot of classical guitar album artwork which usually features the artist in a turtleneck smiling at the camera with guitar in lap).

```html
<!DOCTYPE html>
<html lang="en">
<head>
<meta charset="utf-8">
<title>Dell Corvin – Driftwood CD Sleeve</title>
<link rel="stylesheet" href="https://fonts.googleapis.com/css2?family=Lexend:wght@400;500&family=Kaushan+Script&display=swap">
<style>
  :root {
    --paper: #ffffff;
    --brick-dark: #5a2a18;
    --brick: #8c4428;
    --brick-light: #a65a3a;
    --door-dark: #1e2c3e;
    --door: #34507a;
    --door-light: #5e7f9a;
    --wood: #c89a62;
    --frame: #ffffff;
    --ink: #ffffff;
    --dieline: #e0282e;
    --bleed: #29b6d6;
  }
  * { box-sizing: border-box; margin: 0; padding: 0; }
  html, body { width: 1200px; height: 763px; overflow: hidden; background: var(--paper); }
  .sheet { position: relative; width: 1200px; height: 763px; font-family: "Lexend", sans-serif; }

  .panel { position: absolute; top: 109px; height: 531px; }
  .panel--back { left: 78px; width: 528px;
    background:
      radial-gradient(ellipse at 70% 70%, var(--wood) 0%, rgba(200,154,98,0) 32%),
      radial-gradient(ellipse at 65% 45%, #4b6b8c 0%, rgba(75,107,140,0) 30%),
      linear-gradient(100deg, var(--brick-dark) 0%, var(--brick) 45%, var(--brick-light) 80%, var(--brick) 100%); }
  .panel--front { left: 606px; width: 526px;
    background:
      radial-gradient(ellipse at 78% 80%, var(--wood) 0%, rgba(200,154,98,0) 26%),
      radial-gradient(ellipse at 35% 20%, #6b88a8 0%, rgba(107,136,168,0) 35%),
      linear-gradient(90deg, var(--door-light) 0%, var(--door) 20%, var(--door-dark) 55%, var(--door) 80%, var(--door-dark) 100%); }

  .frame { position: absolute; top: 137px; height: 476px; border: 2.5px solid var(--frame); }
  .frame--back { left: 107px; width: 484px; }
  .frame--front { left: 619px; width: 486px; }

  .tracklist { position: absolute; left: 133px; top: 172px; list-style: none; color: var(--ink);
    font-size: 10.5px; text-transform: uppercase; letter-spacing: 0.1px; }
  .tracklist li { height: 28px; }

  .artist { position: absolute; color: var(--ink); text-transform: uppercase; white-space: nowrap; }
  .artist--back { left: 133px; top: 584px; font-size: 13.5px; letter-spacing: 4.5px; }
  .artist--front { left: 646px; top: 579px; font-size: 19px; letter-spacing: 13.5px; }

  .album-title { position: absolute; left: 655px; top: 205px; color: var(--ink);
    font-family: "Kaushan Script", cursive; font-size: 104px; line-height: 1; transform: rotate(-4deg); }

  .guides { position: absolute; left: 0; top: 0; }
</style>
</head>
<body>
<main class="sheet">
  <div class="panel panel--back" role="img" aria-label="Photo of the guitarist leaning against a red brick wall, playing an acoustic guitar"></div>
  <div class="panel panel--front" role="img" aria-label="Photo of the guitarist standing in front of a blue door, holding an acoustic guitar by the neck"></div>

  <div class="frame frame--back"></div>
  <div class="frame frame--front"></div>

  <ol class="tracklist">
    <li>01 » Orchard Shuffle</li>
    <li>02 » Tumbleweed</li>
    <li>03 » Glimpses of Perlow</li>
    <li>04 » Wound Up</li>
    <li>05 » Walk Along</li>
    <li>06 » The Quiet Ridge</li>
    <li>07 » Unfolding</li>
    <li>08 » Evening on Barrow Lane</li>
    <li>09 » Lucinda's Tune</li>
  </ol>
  <p class="artist artist--back">«Dell Corvin»</p>

  <h1 class="album-title">Driftwood</h1>
  <p class="artist artist--front">« Dell Corvin »</p>

  <svg class="guides" width="1200" height="763" viewBox="0 0 1200 763" aria-hidden="true">
    <rect x="78.5" y="109.5" width="1053" height="530" fill="none" stroke="var(--bleed)" stroke-width="1" stroke-dasharray="4 3"/>
    <rect x="91.5" y="121.5" width="1029" height="506" fill="none" stroke="var(--dieline)" stroke-width="0.7"/>
    <line x1="606" y1="109" x2="606" y2="640" stroke="var(--dieline)" stroke-width="0.7"/>
    <path d="M606 121 L606 109 L615 72 Q617 65 625 65 L1100 65 Q1108 65 1110 72 L1120 109 L1120 121" fill="none" stroke="var(--dieline)" stroke-width="0.8"/>
    <path d="M606 627 L606 640 L615 677 Q617 685 625 685 L1100 685 Q1108 685 1110 677 L1120 640 L1120 627" fill="none" stroke="var(--dieline)" stroke-width="0.8"/>
  </svg>
</main>
</body>
</html>
```